WP website design (Tarnwick)

We need a wordpress design for an established auction and real estate company based in Arkansas. The winning design will incorporate a professional color scheme with company logo in a clean layout. The design needs to consider that this will be developed on a responsive theme.

Industry/Entity Type

Real Estate

Font styles to use
Sans Serif

Colors

Designer to choose colors to be used in the design.

Requirements
Must have
• Site will have slideshow, please use stock real estate or other image. A rough idea of homepage content is attached - not necessarily for design purposes.

Navigation Structure is:
1) Home
2) Auctions
3) Services
4) For Sale
5) About Us
6) Ned Videos
7) News & Events
8) Contact Us

Widgets will include:
Social media icons (Facebook, Youtube, RSS)
Testimonials Widget - this should be prominent
Featured Video
Email Signup form (Sign up to receive exclusive email updates for Tarnwick auctions. )
Nice to have
• A drop down menu example
Should not have
• no gavel in the design

```html
<!DOCTYPE html>
<html lang="en">
<head>
<meta charset="utf-8">
<title>Tarnwick Auction &amp; Marketing</title>
<link rel="stylesheet" href="https://fonts.googleapis.com/css2?family=Open+Sans:ital,wght@0,400;0,600;0,700;1,400&display=swap">
<style>
:root{
  --green:#2f8a3b;
  --green-dark:#246c2e;
  --orange:#d9731c;
  --ink:#333;
  --muted:#777;
  --rule:#e2e2e2;
  --nav:#2b2b2b;
  --footer:#262626;
  --band:#eeeeee;
}
*{box-sizing:border-box;margin:0;padding:0}
html,body{width:717px;height:1200px;overflow:hidden}
body{font-family:"Open Sans",Arial,sans-serif;color:var(--ink);background:#fff;font-size:8px;line-height:1.45;position:relative}
.wrap{position:absolute;left:31px;width:654px}
/* header */
.site-header{top:0;height:64px}
.brand{position:absolute;left:0;top:10px}
.brand-name{font-size:32px;font-weight:700;color:var(--green);letter-spacing:1px;line-height:1;text-transform:uppercase}
.brand-sub{font-size:10px;color:var(--green);margin-top:2px;padding-left:4px}
.header-contact{position:absolute;right:0;top:14px;display:flex;align-items:center;gap:10px}
.call{text-align:right;color:var(--ink);font-size:9px;line-height:1.1}
.call strong{display:block;font-size:14px;color:var(--green);font-weight:700}
.social{display:flex;gap:4px}
.social span{width:16px;height:16px;border-radius:2px;display:block}
.main-nav{top:67px;height:22px;background:var(--green);display:flex}
.main-nav a{color:#fff;text-decoration:none;font-size:7.5px;font-weight:600;text-transform:uppercase;padding:0 13px;line-height:22px}
.main-nav a.current{background:var(--nav)}
/* hero */
.hero{top:96px;height:214px;display:flex}
.slide{width:490px;height:214px;position:relative;background:linear-gradient(180deg,#b9cde0 0%,#dfe6d6 38%,#d9a94b 52%,#b77c2b 78%,#8a5a22 100%)}
.slide-caption{position:absolute;left:0;right:0;bottom:0;height:28px;background:rgba(0,0,0,.7);color:#fff;font-size:10px;padding:7px 12px}
.slide-next{position:absolute;right:10px;bottom:7px;width:15px;height:15px;border-radius:50%;background:#fff}
.about{flex:1;background:#f3f3f3;padding:10px 10px;position:relative}
.about h3{font-size:10px;color:var(--green);margin-bottom:4px}
.about p{font-size:6.5px;color:var(--muted);width:78px}
.portrait{position:absolute;right:8px;top:26px;width:70px;height:95px;background:linear-gradient(180deg,#e9edf0,#8e98a3)}
/* testimonials */
.testimonials{top:322px;text-align:center}
.testimonials h2{font-size:11px;color:var(--green);font-weight:600}
.testimonials p{font-size:7.5px;font-style:italic;color:var(--muted);width:560px;margin:3px auto}
.testimonials .client{font-style:normal;color:var(--ink);font-size:8px}
.dots{display:flex;justify-content:center;gap:4px;margin-top:4px}
.dots i{width:5px;height:5px;border-radius:50%;background:#ccc}
.dots i.on{background:var(--green)}
/* auctions */
.section-title{font-size:14px;font-weight:600;color:var(--green)}
.auctions{top:428px;height:540px;border:1px solid var(--rule);padding:8px 12px}
.auctions-head{border-bottom:1px solid var(--rule);padding-bottom:6px;margin-bottom:8px}
.lot{display:flex;gap:12px;height:118px;padding:8px 0;border-bottom:1px solid var(--rule)}
.lot:last-child{border-bottom:0}
.lot-photo{width:150px;height:100px;flex:none}
.lot-body{flex:1}
.lot-body h4{font-size:10px;color:var(--orange);font-weight:600;margin-bottom:3px}
.lot-body p{font-size:6.8px;color:var(--muted);margin-bottom:9px}
.lot-actions{display:flex;align-items:center;gap:18px;border-top:1px solid var(--rule);padding-top:6px}
.lot-actions a{font-size:7.5px;font-weight:700;color:var(--green-dark);text-decoration:none;text-transform:uppercase;display:flex;align-items:center;gap:4px}
.share{margin-left:auto;display:flex;gap:3px}
.share span{width:16px;height:9px;background:#dadada;border-radius:1px;display:block}
/* videos */
.videos{top:985px;display:flex;gap:20px}
.videos p{font-size:7px;color:var(--muted);margin-top:6px;width:440px}
.video-thumb{width:170px;height:84px;position:relative;background:linear-gradient(180deg,#c7d3db,#7b8a5a 60%,#5b5132)}
.video-thumb::after{content:"";position:absolute;left:72px;top:28px;width:28px;height:28px;border-radius:50%;background:rgba(0,0,0,.6)}
.play{position:absolute;left:82px;top:35px;z-index:1}
/* newsletter */
.newsletter{position:absolute;left:0;top:1100px;width:717px;height:44px;background:var(--band);border-top:1px solid #ddd}
.newsletter .inner{left:31px;top:12px;height:20px;display:flex;align-items:center;gap:12px}
.newsletter h5{font-size:13px;font-weight:400;color:var(--ink)}
.newsletter .field{width:110px;height:18px;background:#fff;border:1px solid #ccc;font-size:6.5px;color:#999;padding:4px}
.newsletter .go{width:14px;height:18px;background:var(--green);margin-left:-12px}
.newsletter .social{position:absolute;right:0;top:0}
.newsletter .social span{width:20px;height:20px;background:#fff;border:1px solid #ccc}
/* footer */
.site-footer{position:absolute;left:0;top:1144px;width:717px;height:56px;background:var(--footer);text-align:center;padding-top:12px}
.site-footer nav a{color:#ccc;font-size:7px;text-decoration:none;margin:0 6px}
.site-footer small{display:block;color:#999;font-size:7px;margin-top:6px}
</style>
</head>
<body>

<header class="wrap site-header">
  <div class="brand">
    <div class="brand-name">Tarnwick</div>
    <div class="brand-sub">Auction &amp; Marketing, LLC</div>
  </div>
  <div class="header-contact">
    <div class="call">Call us Today!<strong>555 014 27390</strong></div>
    <div class="social">
      <span style="background:#3b5b98"></span>
      <span style="background:#c4302b"></span>
      <span style="background:#f28c1c"></span>
    </div>
  </div>
</header>

<nav class="wrap main-nav">
  <a class="current" href="#">Home</a><a href="#">Auctions</a><a href="#">Services</a><a href="#">For Sale</a><a href="#">About Us</a><a href="#">Ned Videos</a><a href="#">News &amp; Events</a><a href="#">Contact Us</a>
</nav>

<section class="wrap hero">
  <div class="slide" role="img" aria-label="Country road through golden farm fields under a blue sky">
    <div class="slide-caption">Suspendisse diam purus, scelerisque vel fringilla</div>
    <span class="slide-next"></span>
  </div>
  <aside class="about">
    <h3>About Ned Halloran</h3>
    <p>Maecenas et mi nec nibh pretium luctus. Curabitur consectetur sed nisl quam. Nam ac lorem sit amet velit feugiat. Nulla vestibulum sed dictum tempor mi tristique.</p>
    <div class="portrait" role="img" aria-label="Portrait of the auctioneer in a suit"></div>
  </aside>
</section>

<section class="wrap testimonials">
  <h2>Client's Testimonials</h2>
  <p>Morbi aliquet rhoncus elit in dignissim. Maecenas ornare tempus leo, quis faucibus libero dignissim ut. Ut consectetur tincidunt felis, eget rhoncus sem placerat ut. Aliquam in sapien dignissim, egestas velit eget, consectetur nisl. Curabitur tincidunt, leo et semper posuere, orci libero feugiat nibh, eu convallis magna.</p>
  <p class="client">Client name,City</p>
  <div class="dots"><i class="on"></i><i></i><i></i></div>
</section>

<section class="wrap auctions">
  <div class="auctions-head"><h2 class="section-title">Current Auctions</h2></div>

  <article class="lot">
    <div class="lot-photo" role="img" aria-label="Green crop rows on farmland" style="background:linear-gradient(180deg,#a9c3d9 0%,#cfdbe2 35%,#6e9a3e 45%,#3f6b24 100%)"></div>
    <div class="lot-body">
      <h4>Aenean dapibus pretium</h4>
      <p>Phasellus quis egestas nulla. In id porttitor libero, a vulputate nisi. Ut gravida diam sit amet turpis faucibus, at venenatis neque dignissim. Donec non dignissim arcu. Aenean nibh neque, dignissim nec accumsan sit amet, pulvinar ultrices massa. Proin tellus quam, mollis id finibus sit amet, ut mollis lacus. Cum sociis natoque penatibus et magnis dis parturient.</p>
      <div class="lot-actions">
        <a href="#"><svg width="8" height="8" viewBox="0 0 8 8"><path d="M1 7l1-3 4-4 2 2-4 4z" fill="currentColor"/></svg>Book Now</a>
        <a href="#"><svg width="9" height="8" viewBox="0 0 9 8"><rect x="0" y="1" width="9" height="7" fill="currentColor"/><circle cx="4.5" cy="4.5" r="1.8" fill="#fff"/></svg>Photo Gallery</a>
        <a href="#"><svg width="7" height="8" viewBox="0 0 7 8"><rect width="7" height="8" fill="currentColor"/><path d="M1.5 3h4M1.5 5h4" stroke="#fff"/></svg>Details</a>
        <div class="share"><span></span><span></span><span></span><span></span></div>
      </div>
    </div>
  </article>

  <article class="lot">
    <div class="lot-photo" role="img" aria-label="Golden wheat field with wooden fence" style="background:linear-gradient(180deg,#8fb0cf 0%,#d6dfe3 35%,#d7a84c 50%,#9b6a2a 100%)"></div>
    <div class="lot-body">
      <h4>Aenean dapibus pretium</h4>
      <p>Phasellus quis egestas nulla. In id porttitor libero, a vulputate nisi. Ut gravida diam sit amet turpis faucibus, at venenatis neque dignissim. Donec non dignissim arcu. Aenean nibh neque, dignissim nec accumsan sit amet, pulvinar ultrices massa. Proin tellus quam, mollis id finibus sit amet, ut mollis lacus. Cum sociis natoque penatibus et magnis dis parturient.</p>
      <div class="lot-actions">
        <a href="#"><svg width="8" height="8" viewBox="0 0 8 8"><path d="M1 7l1-3 4-4 2 2-4 4z" fill="currentColor"/></svg>Book Now</a>
        <a href="#"><svg width="9" height="8" viewBox="0 0 9 8"><rect x="0" y="1" width="9" height="7" fill="currentColor"/><circle cx="4.5" cy="4.5" r="1.8" fill="#fff"/></svg>Photo Gallery</a>
        <a href="#"><svg width="7" height="8" viewBox="0 0 7 8"><rect width="7" height="8" fill="currentColor"/><path d="M1.5 3h4M1.5 5h4" stroke="#fff"/></svg>Details</a>
        <div class="share"><span></span><span></span><span></span><span></span></div>
      </div>
    </div>
  </article>

  <article class="lot">
    <div class="lot-photo" role="img" aria-label="Farm field at sunset with a tractor" style="background:linear-gradient(180deg,#e8b55a 0%,#f2d38a 30%,#9c7a34 55%,#5d4a22 100%)"></div>
    <div class="lot-body">
      <h4>Aenean dapibus pretium</h4>
      <p>Phasellus quis egestas nulla. In id porttitor libero, a vulputate nisi. Ut gravida diam sit amet turpis faucibus, at venenatis neque dignissim. Donec non dignissim arcu. Aenean nibh neque, dignissim nec accumsan sit amet, pulvinar ultrices massa. Proin tellus quam, mollis id finibus sit amet, ut mollis lacus. Cum sociis natoque penatibus et magnis dis parturient.</p>
      <div class="lot-actions">
        <a href="#"><svg width="8" height="8" viewBox="0 0 8 8"><path d="M1 7l1-3 4-4 2 2-4 4z" fill="currentColor"/></svg>Book Now</a>
        <a href="#"><svg width="9" height="8" viewBox="0 0 9 8"><rect x="0" y="1" width="9" height="7" fill="currentColor"/><circle cx="4.5" cy="4.5" r="1.8" fill="#fff"/></svg>Photo Gallery</a>
        <a href="#"><svg width="7" height="8" viewBox="0 0 7 8"><rect width="7" height="8" fill="currentColor"/><path d="M1.5 3h4M1.5 5h4" stroke="#fff"/></svg>Details</a>
        <div class="share"><span></span><span></span><span></span><span></span></div>
      </div>
    </div>
  </article>

  <article class="lot">
    <div class="lot-photo" role="img" aria-label="Combine harvester working a brown field" style="background:linear-gradient(180deg,#c2ccd2 0%,#dcdcd4 30%,#8d7a55 50%,#5b4a30 100%)"></div>
    <div class="lot-body">
      <h4>Aenean dapibus pretium</h4>
      <p>Phasellus quis egestas nulla. In id porttitor libero, a vulputate nisi. Ut gravida diam sit amet turpis faucibus, at venenatis neque dignissim. Donec non dignissim arcu. Aenean nibh neque, dignissim nec accumsan sit amet, pulvinar ultrices massa. Proin tellus quam, mollis id finibus sit amet, ut mollis lacus. Cum sociis natoque penatibus et magnis dis parturient.</p>
      <div class="lot-actions">
        <a href="#"><svg width="8" height="8" viewBox="0 0 8 8"><path d="M1 7l1-3 4-4 2 2-4 4z" fill="currentColor"/></svg>Book Now</a>
        <a href="#"><svg width="9" height="8" viewBox="0 0 9 8"><rect x="0" y="1" width="9" height="7" fill="currentColor"/><circle cx="4.5" cy="4.5" r="1.8" fill="#fff"/></svg>Photo Gallery</a>
        <a href="#"><svg width="7" height="8" viewBox="0 0 7 8"><rect width="7" height="8" fill="currentColor"/><path d="M1.5 3h4M1.5 5h4" stroke="#fff"/></svg>Details</a>
        <div class="share"><span></span><span></span><span></span><span></span></div>
      </div>
    </div>
  </article>
</section>

<section class="wrap videos">
  <div>
    <h2 class="section-title" style="text-transform:uppercase;font-size:12px">Tarnwick's Videos</h2>
    <p>Suspendisse diam purus, scelerisque vel fringilla sed, aliquet sit amet tortor. Pellentesque malesuada eu mauris at ultrices. Donec bibendum, mauris at molestie scelerisque, nisl est ultrices urna, sit amet sagittis est augue eget lectus. Etiam non ultricies eros. Maecenas mattis, elit id porttitor vestibulum, leo elit posuere massa, a semper urna turpis vitae nunc. Donec non nunc sed quam imperdiet vehicula. Cum sociis natoque penatibus et magnis dis parturient montes.</p>
  </div>
  <div class="video-thumb" role="img" aria-label="Featured auction video still of open farmland">
    <svg class="play" width="12" height="14" viewBox="0 0 12 14"><path d="M0 0l12 7-12 7z" fill="#fff"/></svg>
  </div>
</section>

<section class="newsletter">
  <div class="wrap inner">
    <svg width="22" height="16" viewBox="0 0 22 16"><rect x="1" y="1" width="20" height="14" fill="#333"/><path d="M1 1l10 8 10-8" stroke="#eee" stroke-width="1.5" fill="none"/></svg>
    <h5>Newsletter Subscribe</h5>
    <div class="field">Enter your email ID</div>
    <div class="go"></div>
    <div class="social"><span></span><span></span><span></span><span></span><span></span></div>
  </div>
</section>

<footer class="site-footer">
  <nav><a href="#">Home</a><a href="#">Auctions</a><a href="#">Services</a><a href="#">For Sale</a><a href="#">About Us</a><a href="#">Ned Videos</a><a href="#">News &amp; Events</a><a href="#">Contact Us</a></nav>
  <small>Copyright © 2014 Tarnwick Auctions &nbsp; All rights reserved</small>
</footer>

</body>
</html>
```